Pop up exhibition stand 2000mm (H) x 800mm (W)

I would like a simple pop up banner stand for an exhibition.

We need a pop up banner stand design for 'Brisk Forge Processing'

the size is 2000mm(H) x 800mm (W)

Ad copy as follows :

[Brisk Forge logo]

From Sheet Metal To Large Sand Castings

Our Capacity and Rapid Quenching drop bottom ovens deliver precise processing.
We also serve the leading names in aerospace, automotive and advanced engineering.

Visit www.briskforge.example/ or call us Tel: +44 (0)1632 960418

[Put the crafted by the vale logo here, also include the text member somewhere close]

check on their website for other ideas that can help you with this project.

Target Market(s)

will be used at a trade show

Requirements
Nice to have
• modern design for UK manufacturing business

```html
<!DOCTYPE html>
<html lang="en">
<head>
<meta charset="utf-8">
<title>Brisk Forge Processing – Exhibition Stand</title>
<link href="https://fonts.googleapis.com/css2?family=Open+Sans:ital,wght@0,400;0,600;0,700;0,800;1,600;1,700&display=swap" rel="stylesheet">
<style>
  :root {
    --red: #d7191f;
    --red-deep: #b51218;
    --white: #ffffff;
    --ink: #333333;
    --grey: #8c8c8c;
    --frame: #9a9a9a;
  }
  * { margin: 0; padding: 0; box-sizing: border-box; }
  html, body { width: 1200px; height: 2984px; overflow: hidden; background: var(--white); }
  body { font-family: "Open Sans", Arial, sans-serif; }
  .stand { position: relative; width: 1200px; height: 2984px; overflow: hidden; background: var(--red); }
  .backdrop { position: absolute; inset: 0; }

  .brand { position: absolute; left: 70px; top: 60px; display: flex; align-items: center; gap: 24px; }
  .brand-mark { width: 64px; height: 64px; background: var(--red); }
  .brand-name { font-size: 92px; font-weight: 800; color: var(--ink); letter-spacing: -2px; line-height: 1; }
  .tagline { position: absolute; left: 470px; top: 200px; font-style: italic; font-weight: 700; line-height: 1.05; }
  .tagline .lead { display: block; font-size: 54px; color: var(--ink); }
  .tagline .tail { display: block; font-size: 52px; color: var(--red); font-weight: 600; }

  .headline { position: absolute; left: 0; right: 0; top: 572px; text-align: center; color: var(--white); font-weight: 600; line-height: 1.08; }
  .headline .small { font-size: 66px; }
  .headline .big { font-size: 92px; }

  .photo { position: absolute; border: 14px solid var(--frame); }
  .photo-main { left: 80px; top: 832px; width: 1040px; height: 720px; background: linear-gradient(135deg, #3d5f7a 0%, #6f9cc0 45%, #c9cfd3 100%); }
  .photo-left { left: 80px; top: 2088px; width: 512px; height: 360px; background: linear-gradient(135deg, #c9c9c9, #7d7d80 60%, #4d4e52); }
  .photo-right { left: 608px; top: 2088px; width: 512px; height: 360px; background: linear-gradient(135deg, #5b5f63, #9aa3aa 55%, #d8d8d8); }

  .sectors { position: absolute; left: 80px; right: 80px; top: 1590px; display: flex; justify-content: space-between; }
  .sector { width: 300px; text-align: center; color: var(--white); }
  .sector svg { display: block; margin: 0 auto 10px; height: 80px; }
  .sector span { font-size: 26px; font-weight: 700; letter-spacing: 0.5px; }

  .intro { position: absolute; left: 80px; width: 1040px; top: 1760px; color: var(--white); font-size: 49px; line-height: 76px; text-align: justify; }
  .intro strong { font-weight: 800; }

  .contact { position: absolute; left: 80px; right: 80px; top: 2490px; display: flex; align-items: center; justify-content: center; gap: 36px; color: var(--ink); font-size: 42px; font-weight: 600; }
  .contact-item { display: flex; align-items: center; gap: 16px; }
  .divider { width: 3px; height: 80px; background: #bbbbbb; }
  .membership { position: absolute; left: 0; right: 0; top: 2660px; display: flex; align-items: center; justify-content: center; gap: 36px; color: var(--ink); }
  .membership .label { font-size: 34px; font-weight: 600; }
  .partner { display: flex; align-items: center; gap: 18px; }
  .partner-dot { width: 92px; height: 92px; border-radius: 50%; background: var(--red); }
  .partner-name { font-size: 40px; font-weight: 700; color: var(--red); text-transform: uppercase; line-height: 1.05; width: 300px; }
</style>
</head>
<body>
<main class="stand">
  <svg class="backdrop" width="1200" height="2984" viewBox="0 0 1200 2984" aria-hidden="true">
    <path d="M0 0 H1200 V330 C 860 420, 420 470, 0 390 Z" fill="var(--white)"/>
    <path d="M0 360 C 420 450, 860 400, 1200 300 L1200 340 C 860 440, 420 480, 0 400 Z" fill="#c8c8c8" opacity="0.6"/>
    <path d="M0 2468 C 400 2440, 800 2440, 1200 2468 V2840 H0 Z" fill="var(--white)"/>
  </svg>

  <header>
    <div class="brand">
      <div class="brand-mark"></div>
      <div class="brand-name">Brisk Forge</div>
    </div>
    <p class="tagline"><span class="lead">the solution in</span><span class="tail">aluminium heat treatment</span></p>
  </header>

  <h1 class="headline">
    <span class="small">From</span> <span class="big">Sheet Metal</span> <span class="small">To</span><br>
    <span class="big">Large Sand Castings</span>
  </h1>

  <div class="photo photo-main" role="img" aria-label="Technician holding a large cast aluminium ring in front of a blue drop bottom quench furnace"></div>

  <div class="sectors">
    <div class="sector">
      <svg viewBox="0 0 160 80" aria-hidden="true"><path d="M10 52 L150 22 L156 30 L40 62 Z M70 40 L40 12 L56 10 L100 32 Z M62 52 L48 74 L62 72 L86 48 Z M14 50 L6 34 L16 34 L28 46 Z" fill="var(--white)"/></svg>
      <span>AEROSPACE</span>
    </div>
    <div class="sector">
      <svg viewBox="0 0 140 80" aria-hidden="true"><path d="M14 50 Q14 38 30 36 L44 18 Q50 12 60 12 H88 Q98 12 104 20 L116 36 Q128 38 128 50 V60 H14 Z" fill="var(--white)"/><path d="M52 20 H70 V36 H42 Z M78 20 H92 L100 36 H78 Z" fill="var(--red)"/><circle cx="40" cy="62" r="12" fill="var(--white)" stroke="var(--red)" stroke-width="5"/><circle cx="102" cy="62" r="12" fill="var(--white)" stroke="var(--red)" stroke-width="5"/></svg>
      <span>AUTOMOTIVE</span>
    </div>
    <div class="sector">
      <svg viewBox="0 0 120 80" aria-hidden="true"><path d="M8 78 V40 L36 24 V40 L64 24 V40 L84 28 V4 H102 V78 Z" fill="var(--white)"/></svg>
      <span>ENGINEERING</span>
    </div>
  </div>

  <p class="intro">Our <strong>Capacity</strong> and <strong>Rapid Quenching</strong> drop bottom ovens deliver <strong>precise</strong> processing. We also serve the <strong>leading</strong> names in aerospace, automotive and advanced engineering.</p>

  <div class="photo photo-left" role="img" aria-label="Company director standing in the heat treatment workshop"></div>
  <div class="photo photo-right" role="img" aria-label="Operator inspecting parts beside a furnace loading frame"></div>

  <footer>
    <div class="contact">
      <div class="contact-item">
        <svg width="40" height="40" viewBox="0 0 40 40" aria-hidden="true"><circle cx="20" cy="20" r="17" fill="none" stroke="var(--ink)" stroke-width="3"/><path d="M3 20 H37 M20 3 C10 12 10 28 20 37 M20 3 C30 12 30 28 20 37" fill="none" stroke="var(--ink)" stroke-width="3"/></svg>
        <span>www.briskforge.example/</span>
      </div>
      <div class="divider"></div>
      <div class="contact-item">
        <svg width="36" height="40" viewBox="0 0 36 40" aria-hidden="true"><path d="M8 2 L15 10 L11 16 Q15 25 22 29 L28 25 L34 32 L28 38 Q10 36 2 10 Z" fill="var(--ink)"/></svg>
        <span>+44 (0)1632 960418</span>
      </div>
    </div>
    <div class="membership">
      <span class="label">Member</span>
      <div class="divider"></div>
      <div class="partner">
        <div class="partner-dot"></div>
        <div class="partner-name">Crafted by the Vale</div>
      </div>
    </div>
  </footer>
</main>
</body>
</html>
```